Professional Package for CPA Firm

We would like a stationery design for our new CPA Firm based in Atlanta, GA called 'Vale 8'. We work with investors to help grow investments, tax free. We would like the design to have a professional/minimal look with a 'wow' factor. We need 9.5″ x 4.125″, 9x12, and 10x13 mailing envelopes, business cards, and a letterhead. We have a logo that is already complete. For the letterhead, we would like to have space to put credentials at the bottom of the page

Industry/Entity Type

CPA, Accounting

```html
<!DOCTYPE html>
<html lang="en">
<head>
<meta charset="utf-8">
<title>Vale 8 — Business Card</title>
<link rel="stylesheet" href="https://fonts.googleapis.com/css2?family=Montserrat:wght@500;700&family=Roboto:wght@400&display=swap">
<style>
  :root {
    --bg: #1c1f22;
    --card-white: #f4f5f5;
    --teal-deep: #0f4556;
    --teal-darker: #082a36;
    --cyan: #2bb3c0;
    --coral: #e5525c;
    --ink-grey: #6a6f73;
    --divider: #3f6470;
    --back-text: #e6eef0;
  }
  * { box-sizing: border-box; margin: 0; padding: 0; }
  html, body { width: 1200px; height: 900px; overflow: hidden; }
  body {
    background: var(--bg);
    font-family: "Roboto", Arial, sans-serif;
    position: relative;
  }
  .card {
    position: absolute;
    left: 285px;
    width: 630px;
    height: 360px;
    border-radius: 4px;
    overflow: hidden;
    box-shadow: 0 14px 34px rgba(0,0,0,.45);
  }

  /* Front */
  .card-front { top: 70px; background: var(--card-white); }
  .front-band {
    position: absolute; left: 0; right: 0; bottom: 0; height: 40px;
    background: var(--teal-deep);
  }
  .front-band-line {
    position: absolute; left: 0; right: 0; bottom: 45px; height: 4px;
    background: var(--cyan);
  }
  .brand {
    position: absolute; left: 48px; top: 124px; width: 230px;
  }
  .brand-name {
    display: flex; align-items: center; gap: 12px;
    font-family: "Roboto", Arial, sans-serif;
    font-weight: 400; font-size: 40px; line-height: 1;
    color: var(--teal-deep);
  }
  .brand-mark {
    width: 14px; height: 14px; background: var(--coral);
    flex: none;
  }
  .brand-tagline {
    margin-top: 12px;
    font-family: "Montserrat", Arial, sans-serif;
    font-weight: 500; font-size: 14px; color: var(--teal-deep);
    letter-spacing: .5px;
  }
  .divider {
    position: absolute; left: 300px; width: 2px; background: var(--divider);
  }
  .divider-top { top: 78px; height: 40px; }
  .divider-bottom { top: 140px; height: 150px; }
  .contact {
    position: absolute; left: 326px; top: 100px; right: 24px;
  }
  .contact-name {
    font-family: "Montserrat", Arial, sans-serif;
    font-weight: 700; font-size: 19px; letter-spacing: 1px;
    color: var(--teal-deep); text-transform: uppercase;
  }
  .contact-title {
    font-family: "Montserrat", Arial, sans-serif;
    font-weight: 500; font-size: 16px; color: var(--coral);
    margin-top: 2px;
  }
  .contact-address {
    margin-top: 12px; font-size: 15px; line-height: 1.4; color: var(--ink-grey);
  }
  .contact-list { list-style: none; margin-top: 6px; }
  .contact-list li {
    display: flex; align-items: center; gap: 8px;
    font-size: 15px; line-height: 1.5; color: var(--ink-grey);
  }
  .contact-icon { width: 15px; height: 15px; flex: none; }

  /* Back */
  .card-back {
    top: 470px;
    background: radial-gradient(ellipse at 60% 40%, var(--teal-deep), var(--teal-darker));
    display: flex; flex-direction: column; align-items: center; justify-content: center;
  }
  .card-back .brand-name { color: var(--back-text); font-size: 56px; gap: 16px; }
  .card-back .brand-mark { width: 18px; height: 18px; }
  .card-back .brand-tagline { color: var(--back-text); font-size: 17px; margin-top: 16px; }
</style>
</head>
<body>
  <section class="card card-front" aria-label="Business card front">
    <div class="brand">
      <div class="brand-name"><span class="brand-mark"></span>Vale 8</div>
      <div class="brand-tagline">CPAs and Tax Advisors</div>
    </div>
    <span class="divider divider-top"></span>
    <span class="divider divider-bottom"></span>
    <div class="contact">
      <h1 class="contact-name">Marcus Hollenbeck</h1>
      <p class="contact-title">Managing Director</p>
      <p class="contact-address">48 Linden Ridge Road,<br>Marietta, GA 30062</p>
      <ul class="contact-list">
        <li>
          <svg class="contact-icon" viewBox="0 0 24 24" aria-hidden="true"><path fill="#2bb3c0" d="M6.6 10.8a15.1 15.1 0 0 0 6.6 6.6l2.2-2.2a1 1 0 0 1 1-.25 11.4 11.4 0 0 0 3.6.57 1 1 0 0 1 1 1V20a1 1 0 0 1-1 1A17 17 0 0 1 3 4a1 1 0 0 1 1-1h3.5a1 1 0 0 1 1 1c0 1.25.2 2.45.57 3.57a1 1 0 0 1-.25 1z"/></svg>
          +14045550187
        </li>
        <li>
          <svg class="contact-icon" viewBox="0 0 24 24" aria-hidden="true"><rect x="2" y="5" width="20" height="14" rx="1.5" fill="#2bb3c0"/><path d="M3 6l9 7 9-7" fill="none" stroke="#f4f5f5" stroke-width="1.6"/></svg>
          hello@vale8advisors.com
        </li>
        <li>
          <svg class="contact-icon" viewBox="0 0 24 24" aria-hidden="true"><g fill="none" stroke="#2bb3c0" stroke-width="1.8"><circle cx="12" cy="12" r="9.5"/><ellipse cx="12" cy="12" rx="4" ry="9.5"/><path d="M2.5 12h19"/></g></svg>
          www.vale8advisors.com
        </li>
      </ul>
    </div>
    <div class="front-band-line"></div>
    <div class="front-band"></div>
  </section>

  <section class="card card-back" aria-label="Business card back">
    <div class="brand-name"><span class="brand-mark"></span>Vale 8</div>
    <div class="brand-tagline">CPAs and Tax Advisors</div>
  </section>
</body>
</html>
```